Defense contractor needs a roll-up for an exhibition

The booth we have booked has only a size of 3m².
So this will be the centerpiece of the whole booth.
We need a roll-up that attracts visitors and at the same time it should contain already designed graphics. These graphics are giving visitors an overview of our system. So it is necessary to have them exposed in a height that the booth personal can conveniently point with its fingers at them.
For information about our company and product visit:
https://www.brellowtrackline.com/
For designing you should use Adobe Illustrator and the templates provided in the zip file, to guarantee a perfect print.
I have supplied my business card that you can copy the logo. As the company logo will be already at the booth nearby the top of the roll-up, you should not place it there. It can be in the middle or at the bottom.
I have uploaded a picture of the booth. The roll up will be placed at the left of the screen and has a size of 80cm x 200cm

Defense

Defense

Serif

0054AA
0677BA
7BADD7
CADEEF
E8F1F8

• you must use the Adobe Illustrator template to have a good printing result
• company logo on the upper side of the roll-up

```html
<!DOCTYPE html>
<html lang="en">
<head>
<meta charset="utf-8">
<title>Brellow Trackline – Advanced Combat Training Systems Roll-up</title>
<link rel="stylesheet" href="https://fonts.googleapis.com/css2?family=Anton&family=Poppins:wght@400;500;600;700;800&family=Roboto+Condensed:wght@400&display=swap">
<style>
  :root {
    --navy: #0b1769;
    --royal: #1a2a8c;
    --band-blue: #1c2e93;
    --lavender: #e6e8f8;
    --black: #000000;
    --white: #ffffff;
    --ink: #111111;
    --stage: #f1f1f3;
  }
  * { margin: 0; padding: 0; box-sizing: border-box; }
  html, body { width: 1200px; height: 4000px; overflow: hidden; }
  body { background: var(--stage); font-family: "Poppins", sans-serif; color: var(--ink); }

  .rollup {
    position: absolute; left: 0; top: 524px;
    width: 1200px; height: 2952px;
    background: var(--white); overflow: hidden;
  }

  /* Header */
  .hero {
    position: absolute; left: 0; top: 0; width: 1200px; height: 800px;
    background: linear-gradient(180deg, var(--navy) 0%, var(--navy) 42%, #2b3d9a 58%, #5a5aa6 68%, #b98aa8 78%, #5d6fc4 90%, #3c58c6 100%);
    z-index: 1;
  }
  .hero-scene {
    position: absolute; left: 0; top: 420px; width: 1200px; height: 380px;
    background:
      radial-gradient(ellipse 420px 120px at 30% 55%, rgba(240,160,160,0.55), rgba(240,160,160,0) 70%),
      radial-gradient(ellipse 380px 110px at 78% 40%, rgba(230,150,170,0.4), rgba(230,150,170,0) 70%),
      linear-gradient(180deg, rgba(20,30,110,0) 0%, rgba(60,90,200,0.35) 100%);
  }
  .hero-vehicle {
    position: absolute; left: 300px; top: 560px; width: 900px; height: 240px;
    background:
      radial-gradient(ellipse 470px 150px at 55% 100%, rgba(0,0,0,1) 0%, rgba(0,0,0,0.95) 55%, rgba(0,0,0,0) 100%);
  }
  .hero-title {
    position: absolute; left: 92px; top: 100px; width: 1030px;
    font-family: "Anton", sans-serif; color: var(--white);
    font-size: 134px; line-height: 124px; letter-spacing: -1px;
    text-transform: uppercase;
  }
  .hero-subtitle {
    position: absolute; left: 92px; top: 368px; width: 1030px;
    font-weight: 800; color: var(--white);
    font-size: 50px; line-height: 60px; white-space: nowrap; letter-spacing: -0.5px;
  }

  .black-band { position: absolute; left: 0; top: 798px; width: 1200px; height: 162px; background: var(--black); z-index: 2; }

  /* System overview */
  .overview {
    position: absolute; left: 0; top: 960px; width: 1200px; height: 815px;
    background: var(--lavender); z-index: 1;
  }
  .overview-graphic {
    position: absolute; left: 40px; top: 60px; width: 1120px; height: 740px;
    background:
      radial-gradient(ellipse 260px 150px at 20% 38%, rgba(175,182,214,0.75), rgba(175,182,214,0) 100%),
      radial-gradient(ellipse 120px 80px at 33% 12%, rgba(190,196,222,0.7), rgba(190,196,222,0) 100%),
      radial-gradient(ellipse 120px 80px at 55% 12%, rgba(190,196,222,0.7), rgba(190,196,222,0) 100%),
      radial-gradient(ellipse 120px 80px at 87% 12%, rgba(190,196,222,0.7), rgba(190,196,222,0) 100%),
      radial-gradient(ellipse 360px 240px at 68% 68%, rgba(160,168,205,0.8), rgba(160,168,205,0) 100%);
  }

  .tagline { position: absolute; left: 0; top: 893px; width: 1200px; height: 122px; z-index: 3; }
  .tagline svg { position: absolute; left: 0; top: 0; }
  .tagline-text {
    position: absolute; left: 0; top: 18px; width: 1200px; text-align: center;
    font-weight: 700; font-size: 45px; line-height: 48px; color: var(--navy); letter-spacing: -0.5px;
  }

  /* Services */
  .services-band { position: absolute; left: 0; top: 1775px; width: 1200px; height: 160px; z-index: 2; }
  .services-band svg { position: absolute; left: 0; top: 0; }
  .services-title {
    position: absolute; left: 0; top: 22px; width: 1200px; text-align: center;
    font-weight: 800; font-size: 104px; line-height: 120px; color: var(--ink); letter-spacing: 1px;
  }
  .services-area { position: absolute; left: 0; top: 1935px; width: 1200px; height: 915px; background: var(--white); z-index: 1; }
  .services-area .tint { position: absolute; left: 0; top: 376px; width: 1200px; height: 539px; background: var(--lavender); }

  .services-box {
    position: absolute; left: 92px; top: 50px; width: 1018px; height: 700px;
    background: var(--white); border: 6px solid var(--ink); border-radius: 44px;
  }
  .services-intro {
    position: absolute; left: 0; top: 22px; width: 100%; text-align: center;
    font-size: 33px; line-height: 44px; font-weight: 400; letter-spacing: -0.3px;
  }
  .services-divider { position: absolute; left: 506px; top: 156px; width: 3px; height: 500px; background: #777; }
  .service { position: absolute; width: 480px; text-align: center; }
  .service svg { display: block; margin: 0 auto; }
  .service-label { font-weight: 600; font-size: 35px; line-height: 44px; margin-top: 10px; }
  .service--warranty { left: 12px; top: 110px; }
  .service--parts { left: 516px; top: 110px; }
  .service--maintenance { left: 12px; top: 410px; }
  .service--logistics { left: 530px; top: 410px; }

  .brand {
    position: absolute; left: 0; top: 800px; width: 1200px; text-align: center;
    font-weight: 800; font-size: 62px; line-height: 80px;
    color: var(--ink); letter-spacing: 1px; text-transform: uppercase;
  }

  /* Footer */
  .footer { position: absolute; left: 0; top: 2850px; width: 1200px; height: 102px; z-index: 2; }
  .footer svg { position: absolute; left: 0; top: 0; }
  .footer-url {
    position: absolute; left: 0; top: 18px; width: 1200px; text-align: center;
    font-family: "Roboto Condensed", sans-serif; font-size: 54px; line-height: 66px; color: var(--white);
  }
</style>
</head>
<body>
<main class="rollup">

  <header class="hero">
    <div class="hero-scene" role="img" aria-label="Sunset sky with pink and blue clouds behind the horizon"></div>
    <div class="hero-vehicle" role="img" aria-label="Black silhouette of a main battle tank against the sunset sky"></div>
    <h1 class="hero-title">Advanced Combat<br>Training Systems</h1>
    <p class="hero-subtitle">FOR REALISTIC COMBAT SIMULATION</p>
  </header>

  <div class="black-band"></div>

  <section class="overview">
    <div class="overview-graphic" role="img" aria-label="Isometric system overview: two training tanks, three target stations and an instructor control truck with monitors and crew"></div>
  </section>

  <div class="tagline">
    <svg width="1200" height="122" viewBox="0 0 1200 122">
      <polygon points="230,0 970,0 935,67 935,122 265,122 265,67" fill="#e6e8f8"/>
    </svg>
    <p class="tagline-text">EQUIP YOUR FIGHTING FORCE<br>WITH PRECISION TRAINING</p>
  </div>

  <div class="services-band">
    <svg width="1200" height="160" viewBox="0 0 1200 160">
      <rect x="0" y="0" width="1200" height="160" fill="#1c2e93"/>
      <polygon points="235,0 965,0 1045,160 155,160" fill="#ffffff"/>
      <polygon points="255,0 275,0 195,160 175,160" fill="#1c2e93"/>
      <polygon points="925,0 945,0 1025,160 1005,160" fill="#1c2e93"/>
    </svg>
    <h2 class="services-title">SERVICES</h2>
  </div>

  <section class="services-area">
    <div class="tint"></div>
    <div class="services-box">
      <p class="services-intro">The signature of the contract is not the end - it is just the<br>beginning of a long-lasting partnership.We offer</p>
      <div class="services-divider"></div>

      <div class="service service--warranty">
        <svg width="200" height="200" viewBox="0 0 200 200" aria-hidden="true">
          <circle cx="100" cy="100" r="94" fill="#1a2a8c" stroke="#111" stroke-width="8"/>
          <circle cx="100" cy="100" r="52" fill="none" stroke="#fff" stroke-width="6" stroke-dasharray="10 6"/>
          <circle cx="100" cy="100" r="36" fill="none" stroke="#fff" stroke-width="5"/>
          <polyline points="84,101 96,113 118,88" fill="none" stroke="#fff" stroke-width="7" stroke-linecap="round" stroke-linejoin="round"/>
        </svg>
        <p class="service-label">Extended<br>Warranty Programs</p>
      </div>

      <div class="service service--parts">
        <svg width="200" height="200" viewBox="0 0 200 200" aria-hidden="true">
          <circle cx="100" cy="100" r="94" fill="#1a2a8c" stroke="#111" stroke-width="8"/>
          <circle cx="96" cy="92" r="50" fill="none" stroke="#fff" stroke-width="6"/>
          <polyline points="96,62 96,94 112,104" fill="none" stroke="#fff" stroke-width="6" stroke-linecap="round"/>
          <path d="M112,134 c0,-12 18,-12 24,0 c6,12 24,12 24,0 c0,-12 -18,-12 -24,0 c-6,12 -24,12 -24,0 z" fill="#1a2a8c" stroke="#fff" stroke-width="6"/>
        </svg>
        <p class="service-label">Long-term Spare<br>Part Services</p>
      </div>

      <div class="service service--maintenance">
        <svg width="200" height="200" viewBox="0 0 200 200" aria-hidden="true">
          <circle cx="100" cy="100" r="94" fill="#1a2a8c" stroke="#111" stroke-width="8"/>
          <rect x="62" y="52" width="70" height="94" rx="6" fill="none" stroke="#fff" stroke-width="6"/>
          <rect x="82" y="44" width="30" height="16" rx="4" fill="#fff"/>
          <line x1="74" y1="80" x2="118" y2="80" stroke="#fff" stroke-width="5"/>
          <line x1="74" y1="98" x2="118" y2="98" stroke="#fff" stroke-width="5"/>
          <line x1="74" y1="116" x2="100" y2="116" stroke="#fff" stroke-width="5"/>
          <line x1="112" y1="140" x2="142" y2="96" stroke="#fff" stroke-width="8" stroke-linecap="round"/>
        </svg>
        <p class="service-label">Maintenance Contracts</p>
      </div>

      <div class="service service--logistics">
        <svg width="200" height="200" viewBox="0 0 200 200" aria-hidden="true">
          <circle cx="100" cy="100" r="94" fill="#1a2a8c" stroke="#111" stroke-width="8"/>
          <path d="M62,102 a38,38 0 0 1 76,0" fill="none" stroke="#fff" stroke-width="7"/>
          <rect x="54" y="96" width="16" height="30" rx="6" fill="#fff"/>
          <rect x="130" y="96" width="16" height="30" rx="6" fill="#fff"/>
          <path d="M138,126 q0,18 -26,20" fill="none" stroke="#fff" stroke-width="5"/>
          <path d="M58,160 q42,-30 84,0" fill="none" stroke="#fff" stroke-width="6"/>
        </svg>
        <p class="service-label">Logistics Support</p>
      </div>
    </div>

    <p class="brand">Brellow Trackline</p>
  </section>

  <footer class="footer">
    <svg width="1200" height="102" viewBox="0 0 1200 102">
      <rect x="0" y="0" width="1200" height="102" fill="#000"/>
      <polygon points="0,20 80,102 0,102" fill="#1c2e93"/>
      <polygon points="1200,20 1120,102 1200,102" fill="#1c2e93"/>
    </svg>
    <p class="footer-url">www.brellowtrackline.com</p>
  </footer>

</main>
</body>
</html>
```